MBR - Stationery Design Project

We need stationery based on our logo.

Company info :
Cabinet Voisard & Associés
Société à responsabilité limitée au capital de 200.000 FCFP
RCS Papeete 27586K - Numéro tahiti K73962
Centre d’affaires OPALE - Rue Gaston Perrin
BP 61384 MAHU POTE - 98752 Papeete
Tahiti - Polynésie française
Tél : +689 40 73 16 48
Fax : +689 40 39 64 91

Industry/Entity Type

It Company

Font styles to use
Sans Serif

```html
<!DOCTYPE html>
<html lang="fr">
<head>
<meta charset="utf-8">
<title>MBR – Papier à en-tête</title>
<link rel="stylesheet" href="https://fonts.googleapis.com/css2?family=Jost:wght@300;400;500&display=swap">
<style>
  :root {
    --backdrop: #dedede;
    --paper: #ffffff;
    --navy: #1b2f55;
    --slate: #879a9b;
    --ink: #1b2f55;
    --muted: #6d7680;
    --ghost: #f0f0f0;
    --rule: #9aa1a8;
  }
  * { box-sizing: border-box; margin: 0; padding: 0; }
  html, body {
    width: 1200px; height: 1000px; overflow: hidden;
    background: var(--backdrop);
    font-family: "Jost", "Century Gothic", sans-serif;
  }
  .letterhead {
    position: absolute; left: 282px; top: 50px;
    width: 636px; height: 900px;
    background: var(--paper);
    box-shadow: 0 2px 10px rgba(0,0,0,0.12);
    overflow: hidden;
  }
  .header-shapes { position: absolute; left: 0; top: 0; }
  .brand { position: absolute; left: 98px; top: 26px; color: var(--ink); }
  .brand-name {
    font-size: 74px; font-weight: 400; line-height: 1; letter-spacing: 2px;
  }
  .brand-firm {
    font-size: 15px; font-weight: 400; line-height: 1.1; margin-top: 2px; margin-left: 8px;
  }
  .brand-tagline {
    font-size: 8px; font-weight: 400; color: var(--muted); margin-left: 8px; letter-spacing: 0.5px;
  }
  .backdrop-mark {
    position: absolute; left: 0; right: 0; top: 300px;
    text-align: center;
    font-size: 210px; font-weight: 300; letter-spacing: 6px;
    color: var(--ghost); line-height: 1;
  }
  .footer { position: absolute; left: 60px; right: 60px; bottom: 52px; text-align: center; }
  .footer-rule { height: 1px; background: var(--rule); margin: 0 20px 7px; }
  .footer-line {
    font-size: 7px; font-weight: 400; color: var(--muted); line-height: 1.6; white-space: nowrap;
  }
</style>
</head>
<body>
  <main class="letterhead">
    <svg class="header-shapes" width="636" height="130" viewBox="0 0 636 130" aria-hidden="true">
      <polygon class="slate-band" points="268,0 636,0 636,62 318,62" fill="var(--slate)"/>
      <rect class="navy-block" x="0" y="60" width="90" height="52" fill="var(--navy)"/>
    </svg>

    <header class="brand">
      <div class="brand-name">MBR</div>
      <div class="brand-firm">Cabinet Voisard &amp; Associés</div>
      <div class="brand-tagline">Expertise-comptable · Audit · Conseil</div>
    </header>

    <div class="backdrop-mark" aria-hidden="true">MBR</div>

    <footer class="footer">
      <div class="footer-rule"></div>
      <p class="footer-line">Cabinet Voisard &amp; Associés - Société à responsabilité limitée au capital de 200.000 FCFP - RCS Papeete 27586K - Numéro tahiti K73962</p>
      <p class="footer-line">Centre d’affaires OPALE - Rue Gaston Perrin BP 61384 MAHU POTE - 98752 Papeete Tahiti - Polynésie française &nbsp;|&nbsp; Tel : +689 40 73 16 48 &nbsp;|&nbsp; Fax : +689 40 39 64 91</p>
    </footer>
  </main>
</body>
</html>
```